Corvel Capital LLC

Need Professional Business cards for New Investment Fund

Target Market(s)

High Quality investors

Industry/Entity Type

Financial

Contact Information for Business Card

Phone Number +1 555 284 6190
Name Lukas Varenko
Title Fund Manager
email lv@FundCorvel.com
Website www.FundCorvel.com

Colors

Designer to choose colors to be used in the design.

Requirements
Must have
• Must have our Logo and all of the above. Must be made so lettering and loge can be raised

```html
<!DOCTYPE html>
<html lang="en">
<head>
<meta charset="utf-8">
<title>Quarvell – Business Card</title>
<link rel="stylesheet" href="https://fonts.googleapis.com/css2?family=Roboto:wght@400;500;700&display=swap">
<style>
  :root {
    --backdrop: #c9c9c9;
    --forest: #39443b;
    --forest-mid: #4a5a44;
    --lime: #86b81e;
    --paper: #f2f2f0;
    --ink-light: #ececec;
    --rule: #c8cec4;
  }
  * { margin: 0; padding: 0; box-sizing: border-box; }
  html, body { width: 1200px; height: 1138px; overflow: hidden; }
  body {
    background: var(--backdrop);
    font-family: "Roboto", sans-serif;
    position: relative;
  }
  .card {
    position: absolute;
    width: 620px;
    height: 374px;
    border-radius: 14px;
  }
  .card-front {
    left: 274px; top: 186px;
    background: var(--forest);
  }
  .brand {
    font-family: "Roboto", sans-serif;
    font-weight: 500;
    text-transform: uppercase;
    letter-spacing: 0.03em;
    display: flex; align-items: center;
    white-space: nowrap;
  }
  .brand-mark {
    display: inline-block;
    flex: none;
    border-radius: 50%;
    background: var(--lime);
  }
  .card-front .brand {
    position: absolute; left: 174px; top: 150px;
    font-size: 42px; line-height: 50px;
    color: var(--ink-light); gap: 14px;
  }
  .card-front .brand-mark { width: 18px; height: 18px; }

  .card-back {
    left: 276px; top: 608px;
    background: var(--paper);
  }
  .card-back .brand {
    position: absolute; left: 44px; top: 82px;
    font-size: 32px; line-height: 38px;
    color: var(--forest); gap: 10px;
  }
  .card-back .brand-mark { width: 13px; height: 13px; }
  .contact-band {
    position: absolute;
    left: 14px; top: 170px;
    width: 590px; height: 188px;
    background:
      radial-gradient(circle at 92% 10%, #8fc21c 0%, #6c9a2e 22%, rgba(74,90,68,0) 60%),
      linear-gradient(90deg, var(--forest) 0%, var(--forest) 45%, var(--forest-mid) 70%, #5f8a30 100%);
    color: var(--ink-light);
  }
  .holder-name {
    position: absolute; left: 30px; top: 20px;
    font-size: 24px; line-height: 30px; font-weight: 700;
  }
  .holder-title {
    position: absolute; left: 30px; top: 56px;
    font-size: 16px; line-height: 20px; font-weight: 400;
  }
  .contact-list {
    position: absolute; left: 30px; top: 96px;
    width: 308px; list-style: none;
  }
  .contact-list li {
    display: flex; align-items: center; gap: 14px;
    height: 26px;
    font-size: 15px;
    border-bottom: 1px solid var(--rule);
  }
  .contact-list li:last-child { border-bottom: none; }
  .contact-list svg { width: 16px; height: 16px; flex: none; fill: var(--ink-light); }
</style>
</head>
<body>
  <section class="card card-front" aria-label="Card front">
    <div class="brand"><span class="brand-mark"></span>Quarvell</div>
  </section>

  <section class="card card-back" aria-label="Card back">
    <div class="brand"><span class="brand-mark"></span>Quarvell</div>
    <div class="contact-band">
      <h1 class="holder-name">Lukas Varenko</h1>
      <p class="holder-title">Fund Manager</p>
      <ul class="contact-list">
        <li>
          <svg viewBox="0 0 16 16" aria-hidden="true"><path d="M2 5c0-2 2-3 6-3s6 1 6 3v1h-3V5H5v1H2z"/><path d="M4 7h8l2 6H2z"/></svg>
          +1 555 284 6190
        </li>
        <li>
          <svg viewBox="0 0 16 16" aria-hidden="true"><path d="M1 3h14v10H1z M2 4l6 5 6-5" fill="none" stroke="#ececec" stroke-width="1.6"/><path d="M1 3h14L8 9z"/></svg>
          lv@FundCorvel.com
        </li>
        <li>
          <svg viewBox="0 0 16 16" aria-hidden="true"><circle cx="8" cy="8" r="6.5" fill="none" stroke="#ececec" stroke-width="1.4"/><ellipse cx="8" cy="8" rx="2.8" ry="6.5" fill="none" stroke="#ececec" stroke-width="1.2"/><path d="M1.5 8h13" stroke="#ececec" stroke-width="1.2"/></svg>
          www.FundCorvel.com
        </li>
      </ul>
    </div>
  </section>
</body>
</html>
```